Its time for a new website

We are at a point now where we are in desperate need of a new website. It was last updated 2006 but still looks like its 1995. We are looking for something eye catching to our clients but easy to navigate and add/remove photos of jobs/trucks and information. Our key business is the manufacture of fire appliances and resale of parts and equipment.

www.kestrelrigs.com.au

Coding

Coded - Design and coding required

Number of Pages Required

5+ page

Requirements
Must have
• Logo

```html
<!DOCTYPE html>
<html lang="en">
<head>
<meta charset="utf-8">
<title>Kestrel Rigs</title>
<link href="https://fonts.googleapis.com/css2?family=Open+Sans:wght@300;400;600;700&display=swap" rel="stylesheet">
<style>
:root{
  --red:#d0121b;
  --blue:#1a6db5;
  --dark:#1b1b1b;
  --nav:#1f1f1f;
  --grey:#ededed;
  --text:#666;
  --heading:#444;
  --footer:#2b2b2b;
  --orange:#f39a12;
}
*{box-sizing:border-box;margin:0;padding:0}
html,body{width:834px;height:1200px;overflow:hidden;background:#fff}
body{font-family:'Open Sans',Arial,sans-serif;position:relative}
.masthead{position:absolute;top:0;left:0;width:834px;height:69px;
  background:radial-gradient(ellipse 420px 60px at 50% 30%,#ffb21c 0%,#e86a0c 45%,#8a1408 80%,#3a0604 100%)}
.brand{position:absolute;left:0;width:834px;top:6px;text-align:center}
.brand-dot{display:block;width:32px;height:32px;border-radius:50%;background:var(--red);margin:0 auto 3px}
.brand-name{font-size:11px;font-weight:400;color:var(--orange);letter-spacing:.5px}
.main-nav{position:absolute;top:69px;left:0;width:834px;height:33px;background:var(--nav);
  display:flex;justify-content:center;gap:0}
.main-nav a{color:#fff;font-size:7.5px;text-decoration:none;line-height:33px;padding:0 14px;text-transform:uppercase}
.main-nav a.active{color:#ff4a3a}
.hero{position:absolute;top:102px;left:0;width:834px;height:306px;
  background:linear-gradient(90deg,#2a2a2a 0%,#7a1a18 30%,#b3221f 55%,#5b1210 80%,#333 100%)}
.hero-title{position:absolute;top:112px;left:0;width:834px;text-align:center;color:#fff;font-size:22px;line-height:37px;font-weight:400}
.hero-dots{position:absolute;top:249px;left:0;width:834px;display:flex;justify-content:center;gap:4px}
.hero-dots span{width:8px;height:8px;border-radius:50%;background:#fff}
.hero-dots span:first-child{background:var(--red)}
.intro{position:absolute;top:408px;left:0;width:834px;height:138px;text-align:center}
.intro h1{margin-top:26px;color:var(--red);font-size:14px;font-weight:600}
.intro h2{margin-top:10px;color:var(--blue);font-size:10.5px;font-weight:400}
.intro p{margin-top:5px;color:#888;font-size:7.5px;line-height:18px;font-weight:300}
.work{position:absolute;top:546px;left:0;width:834px;height:298px;background:var(--grey)}
.work h3{text-align:center;margin-top:21px;color:var(--heading);font-size:13.5px;font-weight:600}
.work .lead{text-align:center;margin-top:12px;color:var(--text);font-size:8px}
.cards{position:absolute;top:98px;left:69px;display:flex;gap:14px}
.card{width:164px}
.card-photo{width:164px;height:113px}
.card h4{color:var(--red);font-size:9.5px;font-weight:400;margin-top:14px}
.card p{color:var(--text);font-size:7px;line-height:17px;margin-top:3px}
.contact{position:absolute;top:844px;left:0;width:834px;height:290px;
  background:linear-gradient(135deg,#e8e4dc,#d9d6cf 50%,#e6e2da)}
.contact-panel{position:absolute;top:30px;left:70px;width:562px;height:232px;background:rgba(80,80,80,.85)}
.contact-panel h3{position:absolute;top:16px;left:0;width:562px;text-align:center;color:#fff;font-size:12px;font-weight:600}
.field{position:absolute;background:#fff;border:1px solid #ccc;color:#999;font-size:7.5px;font-style:italic;padding:8px}
.submit{position:absolute;left:229px;top:199px;width:67px;height:21px;background:var(--blue);color:#fff;
  font-size:7.5px;font-weight:700;text-align:center;line-height:21px;letter-spacing:.5px}
.info{position:absolute;left:330px;color:#fff;font-size:8px;line-height:14px;display:flex;gap:6px}
.info svg{flex:none;margin-top:3px}
.site-footer{position:absolute;top:1134px;left:0;width:834px;height:66px;background:var(--footer)}
.foot-nav{position:absolute;top:16px;left:69px;font-size:7px;color:#ddd}
.foot-nav span{margin:0 4px;color:#aaa}
.copyright{position:absolute;top:41px;left:69px;font-size:7px;color:#888}
.copyright b{color:#fff;font-weight:400}
.social{position:absolute;top:21px;left:638px;display:flex;gap:6px}
.social span{width:21px;height:21px;border-radius:50%;background:#555}
</style>
</head>
<body>
<header class="masthead">
  <div class="brand"><span class="brand-dot"></span><span class="brand-name">Kestrel Rigs</span></div>
</header>
<nav class="main-nav">
  <a class="active">Home</a><a>About us</a><a>Pumpers</a><a>Tankers</a><a>GPA/Resue</a><a>Light Tankers</a><a>Trailers</a><a>Slip-on units</a><a>Contact us</a><a>New for 2006</a>
</nav>
<section class="hero" role="img" aria-label="Photo of a red fire engine driving at speed">
  <div class="hero-title">Kestrel Rigs are Western Australia's<br>leading manufacturer</div>
  <div class="hero-dots"><span></span><span></span><span></span></div>
</section>
<section class="intro">
  <h1>KESTREL RIGS !</h1>
  <h2>Kestrel Rigs are Western Australia's leading manufacturer of custom firefighting equipment</h2>
  <p>Fire-Brigade Captain and 35-year veteran volunteer Fire-fighter, Martin Colby, established Kestrel Rigs in 1988. As a fully Qualified automotive motor<br>an ever increasing range of high Quality, Functional and Affordable fire appliances suited to the harsh Australian environment.!</p>
</section>
<section class="work">
  <h3>ABOUT OUR WORK</h3>
  <p class="lead">Es simplemente el texto de relleno de las imprentas y archivos de texto. Lorem Ipsum ha sido el texto de relleno estándar de las...</p>
  <div class="cards">
    <div class="card"><div class="card-photo" role="img" aria-label="Photo of a red pumper truck" style="background:linear-gradient(#9db5c9,#b52a22 55%,#6d6a5e)"></div><h4>Pumpers</h4><p>Es simplemente el texto de relleno de las imprentas y archivos de texto.</p></div>
    <div class="card"><div class="card-photo" role="img" aria-label="Photo of a white tanker truck" style="background:linear-gradient(#b8c3cc,#dfe1dc 50%,#6c6a60)"></div><h4>Tankers</h4><p>Es simplemente el texto de relleno de las imprentas y archivos de texto.</p></div>
    <div class="card"><div class="card-photo" role="img" aria-label="Photo of a red general purpose appliance" style="background:linear-gradient(#c9c3b6,#b8261f 50%,#7a6f62)"></div><h4>General Purpose</h4><p>Es simplemente el texto de relleno de las imprentas y archivos de texto.</p></div>
    <div class="card"><div class="card-photo" role="img" aria-label="Photo of a white light tanker" style="background:linear-gradient(#a8b6a0,#e6e4df 50%,#7c7568)"></div><h4>Light Tankers</h4><p>Es simplemente el texto de relleno de las imprentas y archivos de texto.</p></div>
  </div>
</section>
<section class="contact" role="img" aria-label="Street map showing the workshop location">
  <div class="contact-panel">
    <h3>CONTACTS</h3>
    <div class="field" style="left:24px;top:54px;width:130px;height:26px">Your name</div>
    <div class="field" style="left:167px;top:54px;width:130px;height:26px">Your email</div>
    <div class="field" style="left:24px;top:94px;width:272px;height:90px">Your message</div>
    <div class="submit">SUBMIT</div>
    <div class="info" style="top:62px;width:200px">
      <svg width="7" height="9" viewBox="0 0 7 9"><path d="M3.5 0A3.5 3.5 0 0 0 0 3.5C0 6 3.5 9 3.5 9S7 6 7 3.5A3.5 3.5 0 0 0 3.5 0zm0 5a1.5 1.5 0 1 1 0-3 1.5 1.5 0 0 1 0 3z" fill="#fff"/></svg>
      <span>Lot 14 Banksia Road Merredin 6415 Western Australia</span>
    </div>
    <div class="info" style="top:101px">
      <svg width="8" height="8" viewBox="0 0 8 8"><rect width="8" height="8" rx="1.5" fill="#fff"/><path d="M2 1.8l1 1-.6.7c.4.9 1 1.5 1.9 1.9l.7-.6 1 1-.8.8C3.5 6.4 1.6 4.5 1.2 2.6z" fill="#555"/></svg>
      <span>08 97340518 &nbsp; fax (Aust) - 08 97340519</span>
    </div>
    <div class="info" style="top:124px">
      <svg width="9" height="7" viewBox="0 0 9 7"><rect x=".5" y=".5" width="8" height="6" fill="none" stroke="#fff"/><path d="M.5.5l4 3 4-3" fill="none" stroke="#fff"/></svg>
      <span>info@kestrelrigs.com.au</span>
    </div>
  </div>
</section>
<footer class="site-footer">
  <div class="foot-nav">HOME<span>/</span>ABOUT US<span>/</span>PUMPERS<span>/</span>TANKERS<span>/</span>GPA/RESUE<span>/</span>LIGHT TANKERS<span>/</span>TRAILERS<span>/</span>SLIP-ON UNITS<span>/</span>CONTACT US</div>
  <div class="copyright">@ 2015. <b>KESTRELRIGS</b>. ALL RIGHTS RESERVED.</div>
  <div class="social"><span></span><span></span><span></span><span></span><span></span></div>
</footer>
</body>
</html>
```